Brightvale cleaning and maintenance company

An expansive website whereby we can advertise our commercial cleaning and maintenance services across a service portfolio of commercial cleaning and property maintenance. Whereby potential skilled resources can deposit there resume so we can collaborate and match candidates to a broad range of cleaning and maintenance jobs/projects.
Updates

Looking for more extensive ideas so the front page can change pictures on it with the focus for Brightvale Commercial Cleaning and Maintenance. Also need to bring in all the portfolios we offer including 1. Equipment Cleaning and Sanitisation Services 2. High pressure gurney and play ground equipment cleaning 3. General Cleaning and Property Facilities Management 4. Project and Recruiting Services, to allow for potential professional cleaners, handy man, mechanics, warehousing resources , electricians to deposit there resume. Most of the designers have stuck with the old portfolio categories , however the portfolio of services we offer has been updated so that needs to be reflected in the website. Also not necessary to use all my original photos I would like the opening page of the website to perhaps be able to change and have different pictures is that possible thank you

```html
<!DOCTYPE html>
<html lang="en">
<head>
<meta charset="utf-8">
<title>Brightvale — Commercial Cleaning &amp; Maintenance</title>
<link href="https://fonts.googleapis.com/css2?family=Noticia+Text:wght@400;700&family=Mulish:wght@400;600&display=swap" rel="stylesheet">
<style>
:root{
  --orange:#f5350a;
  --navy:#0c2a5e;
  --ink:#333;
  --muted:#555;
  --light:#f4f4f4;
  --white:#fff;
}
*{box-sizing:border-box;margin:0;padding:0}
html,body{width:1200px;height:3394px;overflow:hidden;background:var(--white)}
body{position:relative;font-family:"Mulish",sans-serif;color:var(--ink)}

/* header */
.topline{position:absolute;left:0;top:0;width:1200px;height:3px;background:var(--orange)}
.header{position:absolute;left:0;top:3px;width:1200px;height:100px;background:var(--white);border-bottom:1px solid #e6e6e6}
.brand{position:absolute;left:112px;top:30px;display:flex;align-items:center;gap:12px}
.brand-dot{width:38px;height:38px;border-radius:50%;background:var(--navy)}
.brand-name{font-family:"Noticia Text",serif;font-size:38px;color:var(--orange);line-height:1}
.nav{position:absolute;right:112px;top:49px;display:flex;gap:34px;list-style:none}
.nav li{font-family:"Noticia Text",serif;font-size:12.5px;color:#333;letter-spacing:.2px}
.nav li.active{color:var(--orange)}

/* hero */
.hero{position:absolute;left:0;top:103px;width:1200px;height:678px;
  background:linear-gradient(100deg,#eef6fb 0%,#d9eaf5 28%,#7e93a8 45%,#3d4f68 62%,#6b7c92 80%,#d7dde6 100%)}
.hero h1{position:absolute;left:52px;top:188px;font-family:"Noticia Text",serif;font-weight:400;font-size:50px;color:var(--navy);line-height:1}
.hero h1 span{color:var(--orange)}
.hero p{position:absolute;left:52px;top:268px;width:420px;font-family:"Noticia Text",serif;font-size:16px;line-height:33px;color:#222}
.btn{position:absolute;left:53px;top:355px;width:112px;height:46px;background:var(--orange);color:var(--white);font-family:"Noticia Text",serif;font-size:14px;display:flex;align-items:center;justify-content:center}

/* section titles */
.title{position:absolute;left:0;width:1200px;text-align:center;font-family:"Noticia Text",serif;font-weight:400;font-size:38px;color:var(--navy);line-height:1}
.title span{color:var(--orange)}
.rule{position:absolute;left:576px;width:48px;height:2px;background:var(--orange)}

/* services */
.services{position:absolute;left:112px;top:905px;width:976px;height:349px;display:flex;gap:2px}
.service{flex:1;display:flex;flex-direction:column}
.service .photo{height:267px}
.service .label{flex:1;display:flex;flex-direction:column;align-items:center;justify-content:center;color:var(--white);font-family:"Noticia Text",serif;text-align:center}
.label small{font-size:13px;letter-spacing:.2px}
.label strong{font-weight:400;font-size:17px;margin-top:6px}
.label.orange{background:var(--orange)}
.label.navy{background:var(--navy)}

/* resume strip */
.resume{position:absolute;left:112px;top:1270px;width:976px;height:54px;border:1px solid #dcdfe6;display:flex;align-items:center;padding:0 0 0 24px}
.resume h4{font-family:"Noticia Text",serif;font-weight:400;font-size:17px;color:var(--navy);white-space:nowrap}
.resume p{margin-left:18px;font-size:12.5px;color:var(--muted);flex:1}
.resume .submit{width:158px;height:54px;margin-right:-1px;background:var(--orange);color:var(--white);font-family:"Noticia Text",serif;font-size:14px;display:flex;align-items:center;justify-content:center}

/* focus band */
.focus-photo{position:absolute;left:0;top:1338px;width:1200px;height:460px;
  background:linear-gradient(90deg,#5a5f66 0%,#8a7466 22%,#c8653b 32%,#6d6f73 48%,#b9bcc0 70%,#7b8088 100%)}
.focus-box{position:absolute;left:610px;top:1570px;width:478px;height:291px;background:var(--orange)}
.focus-box p{position:absolute;left:58px;top:48px;font-family:"Noticia Text",serif;font-size:32px;line-height:62px;color:var(--white)}
.focus-box svg{position:absolute;left:0;top:0}

/* working with */
.intro{position:absolute;left:200px;top:2001px;width:800px;text-align:center;font-size:13px;line-height:28px;color:var(--muted)}
.pillar{position:absolute;top:2118px;width:260px;text-align:center}
.pillar .icon{width:132px;height:132px;border-radius:50%;margin:0 auto;display:flex;align-items:center;justify-content:center}
.pillar h3{margin-top:18px;font-family:"Noticia Text",serif;font-weight:400;font-size:18px}
.pillar p{margin-top:14px;font-size:12.5px;line-height:25px;color:var(--muted)}
.icon.orange{background:var(--orange)}.icon.navy{background:var(--navy)}
h3.orange{color:var(--orange)}h3.navy{color:var(--navy)}

/* gallery */
.gallery-band{position:absolute;left:0;top:2437px;width:1200px;height:619px;background:var(--light)}
.tile{position:absolute}

/* footer */
.footer{position:absolute;left:0;top:3056px;width:1200px;height:338px;background:var(--navy);color:var(--white)}
.footer .brand{left:112px;top:52px}
.footer .brand-dot{background:var(--white)}
.footer .brand-name{color:var(--white);font-size:42px}
.about{position:absolute;left:112px;top:119px;width:310px;font-size:11.5px;line-height:24px;text-align:justify}
.fcol h4{position:absolute;top:42px;font-family:"Noticia Text",serif;font-weight:400;font-size:18px;letter-spacing:.3px}
.links{position:absolute;left:468px;top:82px;list-style:none}
.links li{font-size:13px;height:28.4px;display:flex;align-items:center}
.links li::before{content:"»";margin-right:18px}
.contact{position:absolute;left:673px;top:82px;list-style:none}
.contact li{font-size:13px;height:28.4px;display:flex;align-items:center;gap:14px}
.contact .indent{padding-left:30px}
.social{position:absolute;left:966px;top:88px}
.social .row{display:flex;align-items:center;gap:12px;height:57.5px}
.social .circ{width:36px;height:36px;border-radius:50%;background:var(--white)}
.social small{display:block;font-size:11.5px;opacity:.85}
.social span{font-size:16px}
.divider{position:absolute;left:112px;top:274px;width:976px;height:1px;background:rgba(255,255,255,.2)}
.copy{position:absolute;left:0;top:300px;width:1200px;text-align:center;font-family:"Noticia Text",serif;font-size:12px}
</style>
</head>
<body>

<div class="topline"></div>
<header class="header">
  <div class="brand"><div class="brand-dot"></div><div class="brand-name">Brightvale</div></div>
  <ul class="nav">
    <li class="active">HOME</li><li>SERVICES</li><li>ABOUT US</li><li>OUR PEOPLE</li><li>SAFETY &amp; COMPLIANCE</li><li>CONTACT</li>
  </ul>
</header>

<section class="hero" role="img" aria-label="Rope-access cleaners washing the glass facade of a tall building">
  <h1>Bright <span>Vale</span></h1>
  <p>Your source for commercial cleaning, equipment sanitisation and property maintenance</p>
  <div class="btn">READ MORE</div>
</section>

<h2 class="title" style="top:819px">Our <span>Services</span></h2>
<div class="rule" style="top:872px"></div>

<div class="services">
  <div class="service">
    <div class="photo" role="img" aria-label="Soft-serve machine being cleaned and sanitised" style="background:linear-gradient(135deg,#c8312a,#f2ede3 55%,#2bb2c9)"></div>
    <div class="label orange"><small>EQUIPMENT CLEANING</small><strong>&amp; SANITISATION</strong></div>
  </div>
  <div class="service">
    <div class="photo" role="img" aria-label="High pressure gurney cleaning of playground equipment" style="background:linear-gradient(135deg,#d9b36a,#6c87b8 50%,#c9c2b4)"></div>
    <div class="label navy"><small>HIGH PRESSURE GURNEY</small><strong>&amp; PLAYGROUND</strong></div>
  </div>
  <div class="service">
    <div class="photo" role="img" aria-label="Clean commercial building interior and facilities" style="background:linear-gradient(160deg,#6a6661,#b9b4ac 50%,#4d4a46)"></div>
    <div class="label orange"><small>GENERAL CLEANING &amp;</small><strong>FACILITIES MANAGEMENT</strong></div>
  </div>
  <div class="service">
    <div class="photo" role="img" aria-label="Maintenance team of tradespeople on a project site" style="background:linear-gradient(135deg,#8d8d8b,#d4d4d2 55%,#9a9a98)"></div>
    <div class="label navy"><small>PROJECT &amp; RECRUITING</small><strong>SERVICES</strong></div>
  </div>
</div>

<div class="resume">
  <h4>Join our team</h4>
  <p>Cleaners, handymen, mechanics, warehousing staff and electricians — deposit your resume and we will match you to jobs.</p>
  <div class="submit">SUBMIT RESUME</div>
</div>

<div class="focus-photo" role="img" aria-label="Worker polishing a shopping centre floor with an orange floor machine"></div>
<div class="focus-box">
  <svg width="478" height="291" viewBox="0 0 478 291" fill="none" stroke="#fff" stroke-width="2">
    <path d="M20 88 V20 H84"/><path d="M458 203 V271 H394"/>
  </svg>
  <p>Our Focus on quality our<br>value add experience and<br>professionalism</p>
</div>

<h2 class="title" style="top:1925px">Working with <span>Brightvale</span></h2>
<div class="rule" style="top:1977px"></div>
<p class="intro">We are Brightvale, a leading, Australian owned, cleaning services company When you work with Brightvale it is easy to do business with us.Our people are professional, reliable and service oriented. In every interaction you have; on site, receiving help from our service support staff, or rolling-out new cleaning sites</p>

<div class="pillar" style="left:140px">
  <div class="icon orange">
    <svg width="60" height="60" viewBox="0 0 60 60" fill="none" stroke="#fff" stroke-width="2.5"><circle cx="27" cy="33" r="20"/><circle cx="27" cy="33" r="12"/><circle cx="27" cy="33" r="4"/><path d="M27 33 L50 10 M44 10 H50 V16"/></svg>
  </div>
  <h3 class="orange">OUR PURPOSE</h3>
  <p>To support and extend the life of equipment, maximize product yield and achieve high quality hygiene</p>
</div>
<div class="pillar" style="left:472px">
  <div class="icon navy">
    <svg width="76" height="50" viewBox="0 0 76 50" fill="none" stroke="#fff" stroke-width="2.5"><path d="M3 25 Q38 -10 73 25 Q38 60 3 25 Z"/><circle cx="38" cy="25" r="12"/><circle cx="38" cy="25" r="5"/></svg>
  </div>
  <h3 class="navy">OUR VISION</h3>
  <p>A sustainable food service and equipment cleaning company that creates value for supports its employees</p>
</div>
<div class="pillar" style="left:805px">
  <div class="icon orange">
    <svg width="60" height="60" viewBox="0 0 60 60" fill="none" stroke="#fff" stroke-width="2.5"><rect x="6" y="8" width="48" height="34"/><path d="M30 42 V50 M22 56 L30 50 L38 56"/><path d="M14 32 Q24 16 40 22"/><circle cx="44" cy="24" r="3"/><path d="M14 14 l5 5 M19 14 l-5 5"/></svg>
  </div>
  <h3 class="orange">OUR STRATEGY</h3>
  <p>To differentiate ourselves through a prevailing focus on customer service, in every interaction we have.</p>
</div>

<div class="gallery-band"></div>
<h2 class="title" style="top:2484px">Our <span>Working</span></h2>
<div class="rule" style="top:2538px"></div>
<div class="tile" role="img" aria-label="Soft-serve machine in a cafe" style="left:112px;top:2571px;width:240px;height:415px;background:linear-gradient(180deg,#6e6861,#c9c3bb 45%,#2a2826)"></div>
<div class="tile" role="img" aria-label="Hand holding a blue slushie cup" style="left:357px;top:2571px;width:485px;height:204px;background:linear-gradient(120deg,#6b3a2c,#2fa99a 55%,#c98c76)"></div>
<div class="tile" role="img" aria-label="Disassembled machine parts laid out for cleaning" style="left:847px;top:2571px;width:241px;height:204px;background:linear-gradient(135deg,#2c2a28,#a8a6a2 50%,#d2b23a)"></div>
<div class="tile" role="img" aria-label="Slushie machine bowls" style="left:357px;top:2782px;width:240px;height:204px;background:linear-gradient(160deg,#2c3d66,#e2e4e8 55%,#6a6a6a)"></div>
<div class="tile" role="img" aria-label="Stainless steel trays after sanitising" style="left:602px;top:2782px;width:240px;height:204px;background:linear-gradient(135deg,#d8d6d2,#8f8c88 55%,#c4c1bc)"></div>
<div class="tile" role="img" aria-label="Cleaned beverage dispenser" style="left:847px;top:2782px;width:241px;height:204px;background:linear-gradient(170deg,#4a3326,#bcb7b0 45%,#1d1b1a)"></div>

<footer class="footer">
  <div class="brand"><div class="brand-dot"></div><div class="brand-name">Brightvale</div></div>
  <p class="about">We are Brightvale, a leading, Australian owned, cleaning services company. When you work with Brightvale it is easy to do business with us.When you work with us it is easy to do business with us.</p>

  <div class="fcol"><h4 style="left:467px">INFORMATION</h4></div>
  <ul class="links"><li>Home</li><li>Services</li><li>About Us</li><li>Our People</li><li>Safety &amp; Compliance</li><li>Contact</li></ul>

  <div class="fcol"><h4 style="left:673px">GET IN TOUCH</h4></div>
  <ul class="contact">
    <li><svg width="14" height="14" viewBox="0 0 14 14" fill="#fff"><path d="M3 1 L5 1 L6 4 L4.5 5.5 Q6 8.5 8.5 9.5 L10 8 L13 9 L13 11 Q12 13 10 13 Q2 11 1 3 Q1 1 3 1Z"/></svg>Office: (07) 5550 1284</li>
    <li><svg width="14" height="14" viewBox="0 0 14 14" fill="#fff"><rect x="1" y="3" width="12" height="9"/><path d="M1 3 L7 8 L13 3" stroke="#0c2a5e" stroke-width="1.4" fill="none"/></svg>Email us : hello@brightvale.example</li>
    <li><svg width="14" height="14" viewBox="0 0 14 14" fill="#fff"><path d="M7 1 A4.5 4.5 0 0 1 11.5 5.5 Q11.5 8 7 13 Q2.5 8 2.5 5.5 A4.5 4.5 0 0 1 7 1Z"/><circle cx="7" cy="5.5" r="1.6" fill="#0c2a5e"/></svg>#145 Lorem Ipsum dummy Text</li>
    <li class="indent">154 Lorem ipsum</li>
  </ul>

  <div class="fcol"><h4 style="left:971px">FOLLOW US</h4></div>
  <div class="social">
    <div class="row"><div class="circ"></div><div><small>Like us on</small><span>Friendpage</span></div></div>
    <div class="row"><div class="circ"></div><div><small>Follow us on</small><span>Chirpline</span></div></div>
    <div class="row"><div class="circ"></div><div><small>Follow us on</small><span>Worknet</span></div></div>
  </div>

  <div class="divider"></div>
  <p class="copy">Copyright © 2020 All right reserved</p>
</footer>

</body>
</html>
```